design a construction company business card

Design business card around our logo. Card must have all the typical info: name, title, address, phone, email, business name, etc. Somewhere on the card I would like to see our motto "Grounded in trust... Driven by dedication." Consider adding a splash of bright orange to the card to complement the blues and silvers/grays in the logo. We are open to metallic inks, textures, etc. We would like to see options on both light and dark backgrounds. The font in the logo is Euro Technic Extended Regular.

```html
<!DOCTYPE html>
<html lang="en">
<head>
<meta charset="utf-8">
<title>Halden Contracting – Business Card</title>
<link rel="stylesheet" href="https://fonts.googleapis.com/css2?family=Source+Sans+3:wght@400;600;700&display=swap">
<style>
  :root {
    --backdrop: #2b2b2d;
    --paper: #ffffff;
    --brand-blue: #1f4fa8;
    --bright-blue: #1a78c2;
    --deep-blue: #1b3f9c;
    --ink-gray: #4a4a4a;
    --soft-gray: #8a8a8a;
  }
  * { margin: 0; padding: 0; box-sizing: border-box; }
  html, body {
    width: 1200px; height: 892px; overflow: hidden;
    background: var(--backdrop);
    font-family: "Source Sans 3", Arial, sans-serif;
  }
  .canvas { position: relative; width: 1200px; height: 892px; }
  .card {
    position: absolute; width: 560px; height: 320px;
    background: var(--paper);
    box-shadow: 0 10px 30px rgba(0,0,0,.5);
    overflow: hidden;
  }
  .card--back { left: 50px; top: 110px; }
  .card--front { left: 590px; top: 462px; }

  .wordmark {
    font-family: "Source Sans 3", Arial, sans-serif;
    font-weight: 700; color: var(--brand-blue);
    display: flex; align-items: center; gap: 10px;
    letter-spacing: 1px; line-height: 1;
  }
  .wordmark__square { width: 14px; height: 14px; background: var(--brand-blue); }
  .card--back .wordmark {
    position: absolute; left: 0; right: 0; top: 120px;
    justify-content: center; font-size: 30px;
  }
  .tagline {
    position: absolute; left: 0; right: 0; top: 205px;
    text-align: center; font-size: 15px; color: var(--ink-gray);
  }

  .card--front .wordmark {
    position: absolute; left: 40px; top: 70px; font-size: 24px;
  }
  .front-art { position: absolute; inset: 0; }
  .contact {
    position: absolute; left: 250px; top: 128px;
    color: var(--ink-gray); font-size: 14px; line-height: 1.25;
  }
  .contact__name { font-weight: 700; font-size: 19px; color: var(--brand-blue); letter-spacing: .5px; }
  .contact__title { font-size: 13px; color: var(--soft-gray); letter-spacing: 1px; margin-bottom: 8px; }
  .contact__label { font-weight: 700; color: var(--brand-blue); }
</style>
</head>
<body>
<main class="canvas">

  <section class="card card--back">
    <div class="wordmark"><span class="wordmark__square"></span>HALDEN CONTRACTING, INC.</div>
    <p class="tagline">Grounded in trust... Driven by dedication.</p>
  </section>

  <section class="card card--front">
    <svg class="front-art" viewBox="0 0 560 320" width="560" height="320" aria-hidden="true">
      <defs>
        <linearGradient id="blockFill" x1="0" y1="0" x2="1" y2="1">
          <stop offset="0" stop-color="var(--bright-blue)"/>
          <stop offset="1" stop-color="var(--deep-blue)"/>
        </linearGradient>
      </defs>
      <rect x="420" y="0" width="90" height="170" fill="url(#blockFill)"/>
      <rect x="60" y="150" width="80" height="152" fill="url(#blockFill)"/>
      <rect x="0" y="302" width="560" height="18" fill="var(--deep-blue)"/>
    </svg>

    <div class="wordmark"><span class="wordmark__square"></span>HALDEN CONTRACTING, INC.</div>

    <div class="contact">
      <p class="contact__name">MARK ELLISON</p>
      <p class="contact__title">PRESIDENT</p>
      <p>4127 Harborview</p>
      <p>Drive Oak Ridge, NY 11020</p>
      <p><span class="contact__label">P:</span> 555 0147 2290</p>
      <p><span class="contact__label">E:</span> mark@halden.com</p>
      <p><span class="contact__label">W:</span> www.halden.com</p>
    </div>
  </section>

</main>
</body>
</html>
```